Honey jar label Wabenglanz beekeeping V1

honey jar labels
500 grams 200mm x 50mm
250 grams 200mm x 30mm

on PDF V1.1. Honey. my ideas are sketched and the photo beautiful flowers has inspired me so far.

Actually, I would like a simple, elegant label.

Of course, you are free to leave out my suggestions and come up with other ideas.

You will find various photos and data and my logo in the upload
The photos are only examples of different flowers / seas of flowers.
There shouldn't be too much grass between the flowers, a little is certainly good depending on the situation.
I don't want any pictures or photos on the label.

We have various types of honey locally, and I would like to illustrate this with flowers, bushes and trees wherever possible!

In the middle of the label only flowers (like in the picture of beautiful flowers in the file) and outside also with shrubs, trees, fir, linden, sycamore, chestnut, etc. These trees do not have to be as present on the outside as the flowers in the middle.

The background of the label can be white or a light yellow/beige...

Address and data are on a PDF see attachment and here

------------------------------------------------------
Left address:
Sprig licensee:
Ruedi Kessler
Morgenweg 27 6253 Gettnau
ruedikessler@postfalke.ch
organic certification CH-Eco-417
--------------------------------------------------------

Center:
Honey (in Shiny Gold Lettering)
and My logo Wabenglanz Imkerei

Right honey info:
Honey should be stored cool
and protected from sunlight.
wabenglanz-imkerei.ch

---------------
Please leave a small space on the left and right for a QR code for the information and address.
---------------
The etiquette viewed from top to bottom:
At the very top maybe a thin line in green or shiny gold

The most difficult part that I have not been convinced of by anyone's version so far.
The middle part with the design with the flowers and the left right outside the bushes and trees
The most difficult part that I have not been satisfied with so far.

The background of the label should be white or in a light yellow / beige...

Below again a thin line of shiny gold,
Then a wider line in green or orange, yellow.. with text inside like
Left: the weight
Right: Lot no. Expiry date
Middle: Summer honey
I think the terra alpin logo also fits in this area.
At the very bottom there is another thin gold line.

Many thanks Ruedi

that spit out chat gpt🐝

Hello Ruedi,

Thank you very much for the detailed description! It sounds like you have a very nice and well thought out label in mind for your honey products. There are some very specific design requests that we can easily implement. I will summarize what you want and give you a few ideas on how the label could be designed.

### Summary of your wishes:
- **Label size and shape**:
- **500 grams**: 200mm x 50mm
- **250 grams**: 200mm x 30mm
- **Background**: White or a very soft yellow/beige.
- **Simple, elegant design**: You want a simple, elegant label with flowers and a soft background. No overly dominant grasses and no photos on the label.
- **Design**:
- In the center: **Beautiful flowers** (as in the picture in the file) that draw the main attention.
- Outside: **Shrubs and trees** such as firs, lindens, sycamores, chestnuts (these should be rather subtle, not have too much presence).
- **Text & Information**:
- **Top**: A thin line in **green or shiny gold**.
- **Middle**: **“Honey”** in shiny gold lettering and your logo (**Wabenglanz beekeeping**).
- **Right**: **Honey info**:
- “Honey should be stored in a cool place and protected from sunlight.”
- Website address (**wabenglanz-imkerei.ch**).
- Space for a **QR code**.
- **Below**:
- A thin line in shiny gold and below it a wider line in **green, orange or yellow** with texts like:
- Left: **Weight**
- Right: **Lot No. **, **Expiration date**
- Middle: **Summer honey**
- **Terra Alpin Logo**
- Another thin gold line at the bottom.
- **Space for QR code**: A small space left for the QR code on the left or right side.

### Design ideas:

1. **Color design**:
- The background in soft beige or white would go well with the natural and elegant effect you want. The flowers in the center could be in soft, natural colors (e.g. purple, pink, yellow), but not too intense so that they don't look too overpowering.
- For the gold accents (e.g. for the lines and the lettering "honey"), a shiny, warm gold could be used to underline the elegance.

2nd **Flowers and plants**:
- The flowers in the middle could be placed in a loose but harmonious arrangement so that they attract the eye but do not appear too “crowded”.
- The trees and shrubs could be subtly hinted at at the edge to give the feeling of a natural, wild environment without overpowering the flowers in the middle. These elements could be kept in more of a green tone to complement the color palette of the flowers.

3. **Fonts and layout**:
- **"Honey"**: An elegant, shiny gold font that is well placed in the center. The font could look modern and classy at the same time to emphasize the high-quality image.
- Your **logo “Wabenglanz Beekeeping”** could be placed directly below the word “Honey”, either in a smaller font or as a watermark-like element.
- The text for storage instructions and website address could be placed at the bottom of the label, in a legible, more classic font.

4. **Lines and accents**:
- A thin line at the top in **green or shiny gold** sets a noble accent and gives the label structure.
- At the bottom, a similar thin line in **gold** and in between a wider line in **green, orange or yellow**, which adds a fresh and lively touch. This wide line could also easily accommodate the text "Summer Honey", the weight, the lot number and the expiration date.

5. **QR code and space for text**:
- The QR code could be placed at the top right or left without overloading the design. It would also be useful to give it a small margin so that it remains easy to read.

### Suggested layout (from top to bottom):

1. **Top**: Thin line in gold or green.
2nd **Top center**: Shiny gold lettering “Honey”.
3. **Middle**: Flower arrangement (harmonious and subtle in color).
4. **Right**: Storage information, website and QR code.
5. **Below**:
- Thin line in gold.
- Wider line in green, yellow or orange with text (weight, lot number, expiration date, organic logo).
- Another thin gold line at the bottom edge.

I hope these suggestions suit your needs! If you need more details or customizations, let me know and I'll be happy to help.

all people who like honey

• Allura Script and Century Gothic Regular

• on PDF V1.1. Honey...... are my ideas sketched and on photo beautiful flowers png file
• The word honey should be in shiny gold letters
• Grass in the center no clouds

```html
<!DOCTYPE html>
<html lang="de">
<head>
<meta charset="utf-8">
<title>Wabenglanz Imkerei – Sommer Honig Etikett</title>
<link rel="stylesheet" href="https://fonts.googleapis.com/css2?family=Montserrat:wght@700&family=Questrial&display=swap">
<style>
  :root {
    --backdrop: #d8d7d3;
    --label-cream: #fdfdf0;
    --gold-dark: #8a6a1e;
    --gold-mid: #c9a54e;
    --gold-light: #efe2b4;
    --brand-gold: #b48a3a;
    --band-green: #1fae35;
    --band-green-dark: #137a24;
    --badge-green: #4a9a3e;
    --shield-tone: #c9cfdc;
    --white: #ffffff;
  }
  * { margin: 0; padding: 0; box-sizing: border-box; }
  html, body {
    width: 1200px; height: 938px; overflow: hidden;
    background: var(--backdrop);
  }
  .label {
    position: absolute; left: 50px; top: 180px;
    width: 1100px; height: 578px;
    background: var(--label-cream);
    font-family: "Questrial", sans-serif;
    overflow: hidden;
  }
  .gold-line {
    position: absolute; left: 0; width: 100%; height: 13px;
    background: linear-gradient(90deg, var(--gold-mid), var(--gold-light) 40%, var(--gold-mid) 70%, var(--gold-light));
  }
  .gold-line.top { top: 0; }
  .gold-line.bottom { top: 562px; height: 16px; }
  .brand {
    position: absolute; left: 0; width: 100%; top: 34px;
    display: flex; flex-direction: column; align-items: center; gap: 8px;
  }
  .brand-dot {
    width: 84px; height: 84px; border-radius: 50%;
    border: 3px solid var(--brand-gold);
  }
  .brand-name {
    color: var(--brand-gold); font-size: 30px; line-height: 1; letter-spacing: 1px;
  }
  .title {
    position: absolute; left: 0; width: 100%; top: 128px;
    text-align: center;
    font-family: "Montserrat", sans-serif; font-weight: 700;
    font-size: 200px; line-height: 270px; letter-spacing: -6px;
    padding-bottom: 10px;
    background: linear-gradient(90deg, var(--gold-dark) 28%, var(--gold-light) 45%, var(--gold-mid) 60%, var(--gold-light) 72%, var(--gold-mid));
    -webkit-background-clip: text; background-clip: text; color: transparent;
    z-index: 2;
  }
  .cert-badge { position: absolute; left: 60px; top: 190px; }
  .region-shield { position: absolute; left: 926px; top: 196px; }
  .meadow {
    position: absolute; left: 0; top: 392px; width: 100%; height: 89px;
    background: linear-gradient(180deg, rgba(253,253,240,0) 0%, rgba(196,214,150,.45) 55%, rgba(150,190,100,.6) 100%),
                linear-gradient(90deg, rgba(230,220,120,.3), rgba(240,190,190,.25) 55%, rgba(240,210,80,.35));
  }
  .band {
    position: absolute; left: 0; top: 481px; width: 100%; height: 81px;
    background: linear-gradient(90deg, var(--band-green-dark), var(--band-green) 20%, var(--band-green) 70%, var(--band-green-dark));
    display: flex; align-items: center; justify-content: center;
  }
  .band-title {
    color: var(--white); font-size: 40px; letter-spacing: 9px;
  }
</style>
</head>
<body>
  <main class="label">
    <div class="gold-line top"></div>

    <div class="brand">
      <div class="brand-dot"></div>
      <div class="brand-name">Wabenglanz Imkerei</div>
    </div>

    <svg class="cert-badge" width="84" height="84" viewBox="0 0 84 84" role="img" aria-label="Bio-Zertifizierungszeichen">
      <circle cx="42" cy="42" r="40" fill="var(--badge-green)"/>
    </svg>

    <svg class="region-shield" width="60" height="66" viewBox="0 0 60 66" role="img" aria-label="Regionales Herkunftszeichen">
      <rect x="0" y="0" width="60" height="66" rx="8" fill="var(--shield-tone)"/>
    </svg>

    <h1 class="title">Honig</h1>

    <div class="meadow" role="img" aria-label="Aquarell-Blumenwiese mit Wildblumen, Gräsern und Sträuchern"></div>

    <div class="band">
      <span class="band-title">SOMMER HONIG</span>
    </div>

    <div class="gold-line bottom"></div>
  </main>
</body>
</html>
```